Luxury Business Card Design for High-End Window Treatments

Gilded Slatworks
Custom Plantation Shutters & Architectural Shading Systems

⸻

BACK

Daniel Trevick
Owner

Custom Interior & Exterior Window Treatments

919-555-0148
gildedslatworks.com

I have included a picture that I’m hoping we can use on the back, but I’m also wondering if you can get rid of the ladder? Should we get rid of shutters , shades and blinds underneath Gilded Slatworks?

Target Market(s)

High-end residential homeowners, custom home builders, architects, interior designers, and luxury renovation clients seeking premium plantation shutters and motorized architectural shading systems.

Industry/Entity Type

Custom Window treatments

Contact Information for Business Card

Front Gilded Slatworks Custom Plantation Shutters Motorized Architectural Shading Systems BACK Daniel Trevick Owner 919-555-0148 GildedSlatworks.com Custom Interior & Exterior Window Treatments By Appointment

Requirements
Nice to have
• Not 100% sure on nice to halves or the color but you can definitely check out my website to get a better understanding of what I’m trying to do

```html
<!DOCTYPE html>
<html lang="en">
<head>
<meta charset="utf-8">
<title>Gilded Slatworks – Business Card</title>
<link rel="stylesheet" href="https://fonts.googleapis.com/css2?family=Open+Sans:wght@400;600;700&display=swap">
<style>
  :root {
    --backdrop: #e6e6e4;
    --card-black: #1b1b1b;
    --gold: #e0b83e;
    --gold-edge: #c9a032;
    --cream: #ece6d8;
    --soft-grey: #c9c9c9;
    --white: #ffffff;
    --sky: #6f9fd6;
    --house-navy: #2c3550;
    --house-trim: #e9e6de;
    --lawn: #5b6b3a;
  }
  * { box-sizing: border-box; margin: 0; padding: 0; }
  html, body {
    width: 1200px; height: 801px; overflow: hidden;
    background: var(--backdrop);
    font-family: "Open Sans", Arial, sans-serif;
  }
  .canvas { position: relative; width: 1200px; height: 801px; }
  .card {
    position: absolute; top: 246px;
    width: 540px; height: 309px;
    background: var(--card-black);
    border: 2px solid var(--gold-edge);
    border-radius: 3px;
    overflow: hidden;
    box-shadow: 0 10px 24px rgba(0,0,0,0.18);
  }
  .card--front { left: 40px; }
  .card--back { left: 620px; }

  /* Front */
  .brand { position: absolute; left: 34px; top: 32px; }
  .brand__name {
    color: var(--cream);
    font-weight: 400; font-size: 34px; line-height: 1.05;
  }
  .brand__offer {
    margin-top: 8px;
    color: var(--gold);
    font-weight: 600; font-size: 15px;
    word-spacing: 14px;
  }
  .person { position: absolute; left: 34px; top: 160px; }
  .person__name {
    color: var(--gold); font-weight: 700; font-size: 22px; letter-spacing: 0.5px;
  }
  .person__role { color: var(--soft-grey); font-size: 16px; margin-top: 1px; }
  .divider {
    position: absolute; left: 34px; right: 30px; top: 224px;
    height: 1px; background: var(--gold);
  }
  .contact {
    position: absolute; left: 34px; top: 236px;
    list-style: none;
    color: var(--soft-grey); font-size: 16px; line-height: 1.55;
  }
  .contact__item { display: flex; align-items: center; gap: 7px; }
  .contact__icon { width: 13px; height: 13px; flex: none; }
  .service-line {
    position: absolute; right: 30px; top: 236px;
    text-align: right;
    color: var(--soft-grey); font-size: 15px; line-height: 1.3;
  }

  /* Back */
  .back__brand {
    position: absolute; left: 0; top: 40px; width: 38%;
    display: flex; flex-direction: column; align-items: center; gap: 12px;
  }
  .back__mark {
    width: 58px; height: 58px; border-radius: 50%;
    border: 2px solid var(--gold);
  }
  .back__name {
    color: var(--cream);
    font-weight: 400; font-size: 22px; line-height: 1.1;
    text-align: center;
  }
  .back__photo {
    position: absolute; top: 0; right: 0; bottom: 0; width: 62%;
    background: linear-gradient(180deg, var(--sky) 0%, var(--house-trim) 22%, var(--house-navy) 45%, #6d6a66 66%, var(--lawn) 85%, #8a8578 100%);
  }
  .back__tagline {
    position: absolute; left: 140px; right: 20px; top: 200px;
    padding: 6px 10px;
    background: rgba(20,20,20,0.55);
    color: var(--white);
    font-size: 14px; line-height: 1.35; font-weight: 600;
    text-align: center;
  }
</style>
</head>
<body>
<main class="canvas">

  <section class="card card--front" aria-label="Business card front">
    <div class="brand">
      <p class="brand__name">Gilded<br>Slatworks</p>
      <p class="brand__offer">Shutters Shades Blinds</p>
    </div>

    <div class="person">
      <p class="person__name">DANIEL TREVICK</p>
      <p class="person__role">Owner</p>
    </div>

    <div class="divider"></div>

    <ul class="contact">
      <li class="contact__item">
        <svg class="contact__icon" viewBox="0 0 16 16" aria-hidden="true">
          <path fill="var(--gold)" d="M3.5 1.5l2.5 0 1 3.5-1.6 1.2a8 8 0 0 0 4.4 4.4L11 9l3.5 1v2.5c0 1-1 2-2 2A11 11 0 0 1 1.5 3.5c0-1 1-2 2-2z"/>
        </svg>
        919-555-0148
      </li>
      <li class="contact__item">
        <svg class="contact__icon" viewBox="0 0 16 16" aria-hidden="true">
          <circle cx="8" cy="8" r="7" fill="var(--gold)"/>
          <path d="M1 8h14M8 1c-3 3.5-3 10.5 0 14M8 1c3 3.5 3 10.5 0 14" stroke="var(--card-black)" stroke-width="1" fill="none"/>
        </svg>
        gildedslatworks.com
      </li>
    </ul>

    <p class="service-line">Custom Interior &amp; Exterior<br>Window Treatments</p>
  </section>

  <section class="card card--back" aria-label="Business card back">
    <div class="back__brand">
      <span class="back__mark" aria-hidden="true"></span>
      <p class="back__name">Gilded<br>Slatworks</p>
    </div>
    <div class="back__photo" role="img" aria-label="Photo of a brick home with a white-trimmed covered porch, shaded windows, landscaped shrubs and white lawn chairs"></div>
    <p class="back__tagline">Custom Plantation Shutters &amp;<br>Motorized Architectural Shading Systems</p>
  </section>

</main>
</body>
</html>
```